Veltrano.co - Polar Expeditions Specialists

We need a modern, visually striking business card for Veltrano.co, a company specialized in selling expedition cruises to the most remote regions on Earth, with a focus on the Arctic and Antarctica. The design should instantly communicate that the cardholder is an expert in polar travel. Use clean, premium aesthetics with cool tones like icy blue and white, possibly incorporating polar imagery (ice, glaciers, penguins, etc.)

Attached the logo

Contact Information for Business Card

Feels high-end and trustworthy.. Visually memorable — encourages people to keep it

Colors
0054AA
0677BA
7BADD7
CADEEF
E8F1F8

Requirements
Must have
• ice, glaciers, penguins, montains
Nice to have
• modern, transparente,

```html
<!DOCTYPE html>
<html lang="en">
<head>
<meta charset="utf-8">
<title>Veltrano.co — Business Card</title>
<link rel="stylesheet" href="https://fonts.googleapis.com/css2?family=Poppins:wght@400;500;600;700;800&display=swap">
<style>
  :root {
    --brand-blue: #3574b6;
    --brand-deep: #0054aa;
    --ice-light: #cadeef;
    --ice-pale: #e8f1f8;
    --paper: #ffffff;
    --ink: #1a1a1a;
    --stage: #2b2b2d;
  }
  * { box-sizing: border-box; margin: 0; padding: 0; }
  html, body {
    width: 1200px; height: 875px; overflow: hidden;
    background: var(--stage);
    font-family: "Poppins", sans-serif;
  }
  .sheet {
    width: 1200px; height: 875px;
    display: flex; flex-direction: column;
    align-items: center; justify-content: center; gap: 56px;
  }
  .card {
    width: 620px; height: 354px;
    border-radius: 24px;
    position: relative; overflow: hidden;
    box-shadow: 0 16px 40px rgba(0,0,0,.45);
  }

  /* Front */
  .card--front { background: var(--brand-blue); color: var(--paper); }
  .front-brand {
    position: absolute; left: 50%; top: 50%;
    transform: translate(-50%, -50%);
    display: flex; align-items: center; gap: 18px;
  }
  .brand-dot {
    width: 44px; height: 44px; border-radius: 50%;
    background: var(--paper); flex: none;
  }
  .front-brand .wordmark { font-size: 64px; font-weight: 800; line-height: 1; letter-spacing: -1px; }
  .front-brand .tagline { font-size: 18px; font-weight: 600; margin-top: 8px; text-align: right; }

  /* Back */
  .card--back { background: var(--paper); color: var(--ink); }
  .back-art {
    position: absolute; right: 0; top: 0;
    width: 250px; height: 100%;
  }
  .back-content {
    position: absolute; left: 44px; top: 58px;
  }
  .back-content .wordmark {
    font-size: 62px; font-weight: 800; color: var(--brand-blue);
    line-height: 1; letter-spacing: -1px;
  }
  .back-content .tagline {
    font-size: 18px; font-weight: 600; color: var(--brand-blue);
    margin-top: 6px; padding-left: 46px;
  }
  .details {
    display: flex; align-items: stretch; gap: 16px;
    margin-top: 26px;
  }
  .holder { text-align: right; align-self: flex-end; }
  .holder .name { font-size: 24px; font-weight: 700; color: var(--brand-blue); line-height: 1.1; }
  .holder .role { font-size: 13px; font-weight: 500; }
  .divider { width: 1.5px; background: var(--brand-blue); }
  .contacts { list-style: none; font-size: 14px; font-weight: 500; line-height: 1.65; }
  .contacts li { display: flex; align-items: center; gap: 8px; }
  .contacts svg { width: 13px; height: 13px; fill: var(--brand-blue); flex: none; }
  .address {
    font-size: 14px; font-weight: 500; margin-top: 24px; padding-left: 30px;
  }
</style>
</head>
<body>
<main class="sheet">

  <section class="card card--front">
    <div class="front-brand">
      <span class="brand-dot"></span>
      <div>
        <div class="wordmark">Veltrano.co</div>
        <div class="tagline">Polar Expeditions Specialists</div>
      </div>
    </div>
  </section>

  <section class="card card--back">
    <svg class="back-art" viewBox="0 0 250 354" role="img" aria-label="Large blue polar bear silhouette with a small bear cub at its side">
      <defs>
        <linearGradient id="artFill" x1="0" y1="0" x2="1" y2="0">
          <stop offset="0" stop-color="#3574b6" stop-opacity="0"/>
          <stop offset=".35" stop-color="#3574b6" stop-opacity=".9"/>
          <stop offset="1" stop-color="#3574b6"/>
        </linearGradient>
      </defs>
      <path d="M40 0 H250 V354 H70 C90 300 70 240 90 180 C110 120 60 60 40 0 Z" fill="url(#artFill)"/>
    </svg>

    <div class="back-content">
      <div class="wordmark">Veltrano.co</div>
      <div class="tagline">Polar Expeditions Specialists</div>

      <div class="details">
        <div class="holder">
          <div class="name">Marcus Ellery</div>
          <div class="role">Managing Director</div>
        </div>
        <span class="divider"></span>
        <ul class="contacts">
          <li><svg viewBox="0 0 24 24"><path d="M6.6 10.8a15.1 15.1 0 0 0 6.6 6.6l2.2-2.2a1 1 0 0 1 1-.25 11.4 11.4 0 0 0 3.6.57 1 1 0 0 1 1 1V20a1 1 0 0 1-1 1A17 17 0 0 1 3 4a1 1 0 0 1 1-1h3.5a1 1 0 0 1 1 1c0 1.25.2 2.45.57 3.57a1 1 0 0 1-.25 1z"/></svg>(555)204-7381</li>
          <li><svg viewBox="0 0 24 24"><path d="M2 5h20v14H2z M2 5l10 8 10-8" /></svg>info@veltrano.co</li>
          <li><svg viewBox="0 0 24 24"><circle cx="12" cy="12" r="10"/></svg>www.veltrano.co</li>
        </ul>
      </div>

      <div class="address">48 Harbor View Lane Eastport, ME 04631 USA</div>
    </div>
  </section>

</main>
</body>
</html>
```